Corwin Beacon Lighting - Commercial & Residential Landscape Lighting

Landscape Lighting Services & Design: Create a website for our landscape lighting company. We would like the design to be tailored around this description:
Illuminate with Confidence. Designed with Precision. Installed with Care.
Locally and veteran-owned, we take pride in transforming outdoor spaces through innovative lighting solutions tailored to your vision. From landscape and holiday lighting to permanent installations, our effortless process and expert design deliver breathtaking results and lasting curb appeal. Backed by a lifetime warranty and quarterly service options, our commitment to quality and customer satisfaction is unwavering. Try before you buy and experience your home in a whole new light with our complimentary demo kit — see the stunning effects before you decide.
- Also, add in this information as well; Outdoor Lighting not only beautifies spaces but also significantly enhances safety by illuminating your home or business. Beautifully lit entrances deter potential intruders, making your home a safer place for your loved ones. we also offer quarterly service plans to ensure lighting equipment continues to operate & illuminate effectively throughout the year. Also mention we provide free estimates and we are offering a 10% discount to military, veterans, and first responders.

Target Market(s)

Luxury market

Industry/Entity Type

Landscape Lighting - Residential & Commercial Lighting Services

Coding

Coded - Design and coding required

Number of Pages Required

2 page

Colors
00AB8E
00BBA5
67D7C9
C6EFE9
E9F9F6
59FF00
82FF00
B8FF75
E3FFCB
F4FFEA
FFC000
F8CF3A
FAE287
FDF2CF
FEFAEE

Requirements
Must have
• a lead generation button where people can submit their information for us to reach out to them and schedule their free estimate, homepage, about page, contact page, products and services page, user friendly, easy to navigate, and it also must be engaging and eye popping, as well as appealing to the luxury market. Please use colors; verdent green, dark green, ivory, and sunny yellow. Also, include an about page that references our story; Derek is retired Army and he opened a fitness studio in 2017 with his wife Jolene. He has installed low voltage lighting in every home he lived in and for his friends and family over the years and decided to open his own business because he is passionate about beautifying outdoor landscapes and highlighting a properties full potential, not only in the day but at night as well all while providing safety and security for his clients. Having a deep respect for nature and landscaping, he wants to provide the same care and quality to each of his clients as he has in the fitness industry for decades. He believes small businesses are the back bone of America and he's excited to provide a service that is all to often neglected in the design of a home.
Nice to have
• I would like to have a clear intent and purpose, engaging web design, clear call to action, optimized for search engines, mobile friendy design, security measures, credibility indicators

```html
<!DOCTYPE html>
<html lang="en">
<head>
<meta charset="utf-8">
<title>Corwin Beacon Lighting – Landscape Lighting</title>
<link href="https://fonts.googleapis.com/css2?family=Lexend:wght@300;400;500;600&display=swap" rel="stylesheet">
<style>
:root{
  --canvas:#eeeeee;
  --night:#0d1a2b;
  --night-mid:#16283a;
  --teal:#12b89d;
  --teal-bright:#1fcab2;
  --teal-deep:#0ea88e;
  --teal-card:#16b99e;
  --paper:#f4f5f5;
  --quote-card:#eef8f7;
  --ink:#151c1c;
  --white:#ffffff;
  --star:#12b89d;
}
*{margin:0;padding:0;box-sizing:border-box}
html,body{width:1200px;height:675px;overflow:hidden;background:var(--canvas);font-family:"Lexend",sans-serif;color:var(--ink)}
.stage{position:relative;width:1200px;height:675px;overflow:hidden}

/* ---------- desktop hero ---------- */
.desktop-hero{position:absolute;left:34px;top:197px;width:388px;height:219px;overflow:hidden}
.hero-photo{position:absolute;inset:0;background:linear-gradient(180deg,#0c1828 0%,#142436 45%,#1a2a2c 70%,#0f5a52 90%,#18b39a 100%)}
.brand{position:absolute;display:flex;align-items:center;gap:3px;color:var(--white);font-weight:400;letter-spacing:.04em;white-space:nowrap}
.brand .dot{border-radius:50%;background:var(--white)}
.nav{position:absolute;display:flex;align-items:center;justify-content:space-around;border:.6px solid rgba(255,255,255,.7);border-radius:20px;color:var(--white)}
.nav-cta{position:absolute;background:var(--white);color:var(--ink);border-radius:20px;display:flex;align-items:center;justify-content:center;font-weight:600}
.hero-title{position:absolute;left:0;right:0;text-align:center;color:var(--white);font-weight:600;letter-spacing:.01em}
.hero-sub{position:absolute;left:0;right:0;text-align:center;color:var(--white);font-weight:300;margin:0 auto}
.btn{position:absolute;border-radius:20px;display:flex;align-items:center;justify-content:center;font-weight:600;color:var(--white)}
.btn-primary{background:var(--teal)}
.btn-dark{background:#101a22}

.desktop-hero .brand{left:26px;top:14px;font-size:11px}
.desktop-hero .brand .dot{width:4px;height:4px}
.desktop-hero .nav{left:246px;top:10px;width:86px;height:12px;font-size:3.4px}
.desktop-hero .nav-cta{left:336px;top:10px;width:37px;height:12px;font-size:3.6px}
.desktop-hero .hero-title{top:75px;font-size:17.5px;line-height:1.15}
.desktop-hero .hero-sub{top:136px;width:250px;font-size:8px;line-height:1.05}
.desktop-hero .btn{top:170px;height:18px;width:75px;font-size:5.4px}
.desktop-hero .btn-primary{left:115px}
.desktop-hero .btn-dark{left:200px}

/* ---------- page columns ---------- */
.column{position:absolute;width:329px;overflow:hidden}
.column-main{left:520px;top:74px;height:601px}
.column-side{left:859px;top:0;height:675px}
.page{position:absolute;left:0;width:329px;height:810px}
.column-side .page{top:-134px}
.column-main .page{top:0}

.page-hero{position:absolute;left:0;top:0;width:329px;height:208px;overflow:hidden}
.page-hero .hero-photo{background:linear-gradient(180deg,#0c1828 0%,#142436 50%,#1b2a2a 72%,#0f6a5f 90%,#1ec7af 100%)}
.page-hero .brand{left:22px;top:11px;font-size:9px}
.page-hero .brand .dot{width:3px;height:3px}
.page-hero .nav{left:209px;top:9px;width:72px;height:10px;font-size:2.8px}
.page-hero .nav-cta{left:284px;top:9px;width:32px;height:10px;font-size:3px}
.page-hero .hero-title{top:70px;font-size:14.5px;line-height:1.12}
.page-hero .hero-sub{top:112px;width:210px;font-size:6.8px;line-height:1.05}
.page-hero .btn{top:144px;height:15px;width:63px;font-size:4.5px}
.page-hero .btn-primary{left:97px}
.page-hero .btn-dark{left:168px}

/* about */
.about{position:absolute;left:0;top:208px;width:329px;height:217px;background:linear-gradient(180deg,var(--teal-bright) 0%,var(--teal-deep) 100%)}
.eyebrow{position:absolute;left:27px;display:flex;gap:4px;font-size:3.6px;line-height:1.4;font-weight:300}
.eyebrow::before{content:"";width:3px;height:3px;border-radius:50%;background:var(--ink);margin-top:1px;flex:none}
.about .eyebrow{top:14px}
.about-copy{position:absolute;left:137px;top:16px;width:160px;font-size:5.3px;line-height:1.42;font-weight:300}
.about-link{position:absolute;left:137px;top:74px;width:132px;font-size:5.4px;font-weight:300;border-bottom:.6px solid var(--ink);padding-bottom:3px}
.about-photo-frame{position:absolute;left:27px;top:76px;width:91px;height:121px;border:1px solid var(--white);border-radius:5px;padding:3px}
.about-photo{width:100%;height:100%;border-radius:3px;background:linear-gradient(180deg,#3d5566 0%,#58606a 30%,#8a6a52 45%,#3a4a2c 60%,#26351f 100%)}
.stat{position:absolute;left:137px;font-weight:300}
.stat strong{display:block;font-weight:300;font-size:14px;line-height:1}
.stat span{display:block;font-size:5.5px;margin-top:2px}
.stat-projects{top:95px}
.stat-satisfaction{top:128px}
.stat-veteran{top:159px}

/* services */
.services{position:absolute;left:0;top:425px;width:329px;height:250px;background:var(--paper)}
.services .eyebrow{top:16px}
.services-copy{position:absolute;left:137px;top:17px;width:160px;font-size:5.3px;line-height:1.42;font-weight:300}
.service-grid{position:absolute;left:29px;top:75px;width:274px;height:120px}
.tile-photo{position:absolute;width:64px;border-radius:3px;background:linear-gradient(180deg,#3c5468 0%,#5b606a 28%,#8d6a4f 44%,#34452a 60%,#1f2c19 100%)}
.tile-card{position:absolute;width:64px;height:24px;border-radius:3px;background:var(--teal-card);color:var(--ink);padding:3px 2.5px}
.tile-card h3{font-size:3.7px;font-weight:400;line-height:1.2}
.tile-card p{font-size:1.9px;font-weight:300;line-height:1.35;margin-top:1.4px}
.col1{left:0}.col2{left:68.5px}.col3{left:137px}.col4{left:205.5px}

.cta-row{position:absolute;left:31px;top:225px;width:270px}
.cta-row p{position:absolute;left:0;top:3px;font-size:3.8px;white-space:nowrap}
.cta-row .btn{left:138px;top:0;width:129px;height:13px;font-size:4.4px}

/* testimonials */
.testimonials{position:absolute;left:0;top:675px;width:329px;height:135px}
.testimonials h2{position:absolute;left:0;right:0;top:18px;text-align:center;font-size:7.2px;font-weight:400}
.quote-card{position:absolute;top:34px;width:93px;height:69px;background:var(--quote-card);border-radius:3px;padding:6px 5px}
.quote-card .stars{color:var(--star);font-size:4.4px;letter-spacing:.5px}
.quote-card p{font-size:3.3px;line-height:1.45;font-weight:300;margin-top:4px;color:#444}
.quote-card cite{position:absolute;left:5px;bottom:15px;font-size:3.5px;font-style:normal}
.q1{left:29px}.q2{left:129px}.q3{left:226px}
.dots{position:absolute;top:127px;left:151px;display:flex;gap:2px}
.dots i{width:9px;height:1.2px;background:#cfd6d6}
.dots i:first-child{background:var(--teal)}
</style>
</head>
<body>
<div class="stage">

  <!-- desktop hero -->
  <section class="desktop-hero">
    <div class="hero-photo" role="img" aria-label="Night photo of a large brick home glowing with warm landscape lighting among trees"></div>
    <div class="brand"><span>CORWIN BEACON</span><span class="dot"></span></div>
    <nav class="nav"><span>Home</span><span>About</span><span>Services</span><span>Our Work</span><span>Contact</span></nav>
    <div class="nav-cta">Free Estimate</div>
    <h1 class="hero-title">Illuminate Your World with<br>Signature Precision.</h1>
    <p class="hero-sub">Luxury landscape lighting that blends design, safety, and timeless beauty.</p>
    <div class="btn btn-primary">Request Free Estimate</div>
    <div class="btn btn-dark">Try Our Demo Kit</div>
  </section>

  <!-- page, main column -->
  <div class="column column-main">
    <div class="page">
      <section class="page-hero">
        <div class="hero-photo" role="img" aria-label="Night photo of a large brick home glowing with warm landscape lighting among trees"></div>
        <div class="brand"><span>CORWIN BEACON</span><span class="dot"></span></div>
        <nav class="nav"><span>Home</span><span>About</span><span>Services</span><span>Our Work</span><span>Contact</span></nav>
        <div class="nav-cta">Free Estimate</div>
        <h1 class="hero-title">Illuminate Your World with<br>Signature Precision.</h1>
        <p class="hero-sub">Luxury landscape lighting that blends design, safety, and timeless beauty.</p>
        <div class="btn btn-primary">Request Free Estimate</div>
        <div class="btn btn-dark">Try Our Demo Kit</div>
      </section>

      <section class="about">
        <div class="eyebrow"><span>Lighting with Purpose,<br>Built on Trust</span></div>
        <p class="about-copy">Lighting is more than beauty — it’s purpose.<br>At Corwin Beacon Lighting, we design and install outdoor lighting that enhances safety, elegance, and your home’s full potential — day and night.Veteran-owned. Detail-driven. Always dependable.</p>
        <div class="about-link">Let us illuminate your property’s true potential →</div>
        <div class="about-photo-frame"><div class="about-photo" role="img" aria-label="Dusk photo of a lit brick house with a wide lawn"></div></div>
        <div class="stat stat-projects"><strong>500+</strong><span>Projects Completed</span></div>
        <div class="stat stat-satisfaction"><strong>98%</strong><span>Client Satisfaction</span></div>
        <div class="stat stat-veteran"><strong>Veteran-Owned</strong><span>&amp; Operated</span></div>
      </section>

      <section class="services">
        <div class="eyebrow"><span>Our Signature Lighting Services</span></div>
        <p class="services-copy">We provide tailored outdoor lighting solutions designed to enhance beauty, functionality, and safety — for homes, businesses, and every space in between.</p>
        <div class="service-grid">
          <div class="tile-photo col1" style="top:0;height:86px" role="img" aria-label="Lit house at dusk"></div>
          <div class="tile-card col1" style="top:92px"><h3>Landscape Lighting</h3><p>Enhance the beauty and visibility of your home’s exterior, pathways, and gardens with energy-efficient landscape lighting.</p></div>
          <div class="tile-card col2" style="top:0"><h3>Holiday &amp; Seasonal Lighting</h3><p>Celebrate every season with customized lighting displays — from festive holidays to special occasions.</p></div>
          <div class="tile-photo col2" style="top:31px;height:86px" role="img" aria-label="Lit house at dusk"></div>
          <div class="tile-photo col3" style="top:0;height:86px" role="img" aria-label="Lit house at dusk"></div>
          <div class="tile-card col3" style="top:92px"><h3>Permanent Installations</h3><p>Long-lasting, low-voltage lighting systems designed to elevate your curb appeal and provide security all year long.</p></div>
          <div class="tile-card col4" style="top:0"><h3>Maintenance &amp; Service Plans</h3><p>Quarterly service options to keep your lighting system running smoothly, season after season.</p></div>
          <div class="tile-photo col4" style="top:33px;height:86px" role="img" aria-label="Lit house at dusk"></div>
        </div>
        <div class="cta-row"><p>Ready to see your home in a whole new light?</p><div class="btn btn-primary">Request a Custom Quote</div></div>
      </section>
    </div>
  </div>

  <!-- page, side column (continued) -->
  <div class="column column-side">
    <div class="page">
      <section class="page-hero">
        <div class="hero-photo" role="img" aria-label="Night photo of a large brick home glowing with warm landscape lighting among trees"></div>
        <div class="btn btn-primary">Request Free Estimate</div>
        <div class="btn btn-dark">Try Our Demo Kit</div>
      </section>

      <section class="about">
        <div class="eyebrow"><span>Lighting with Purpose,<br>Built on Trust</span></div>
        <p class="about-copy">Lighting is more than beauty — it’s purpose.<br>At Corwin Beacon Lighting, we design and install outdoor lighting that enhances safety, elegance, and your home’s full potential — day and night.Veteran-owned. Detail-driven. Always dependable.</p>
        <div class="about-link">Let us illuminate your property’s true potential →</div>
        <div class="about-photo-frame"><div class="about-photo" role="img" aria-label="Dusk photo of a lit brick house with a wide lawn"></div></div>
        <div class="stat stat-projects"><strong>500+</strong><span>Projects Completed</span></div>
        <div class="stat stat-satisfaction"><strong>98%</strong><span>Client Satisfaction</span></div>
        <div class="stat stat-veteran"><strong>Veteran-Owned</strong><span>&amp; Operated</span></div>
      </section>

      <section class="services">
        <div class="eyebrow"><span>Our Signature Lighting Services</span></div>
        <p class="services-copy">We provide tailored outdoor lighting solutions designed to enhance beauty, functionality, and safety — for homes, businesses, and every space in between.</p>
        <div class="service-grid">
          <div class="tile-photo col1" style="top:0;height:86px" role="img" aria-label="Lit house at dusk"></div>
          <div class="tile-card col1" style="top:92px"><h3>Landscape Lighting</h3><p>Enhance the beauty and visibility of your home’s exterior, pathways, and gardens with energy-efficient landscape lighting.</p></div>
          <div class="tile-card col2" style="top:0"><h3>Holiday &amp; Seasonal Lighting</h3><p>Celebrate every season with customized lighting displays — from festive holidays to special occasions.</p></div>
          <div class="tile-photo col2" style="top:31px;height:86px" role="img" aria-label="Lit house at dusk"></div>
          <div class="tile-photo col3" style="top:0;height:86px" role="img" aria-label="Lit house at dusk"></div>
          <div class="tile-card col3" style="top:92px"><h3>Permanent Installations</h3><p>Long-lasting, low-voltage lighting systems designed to elevate your curb appeal and provide security all year long.</p></div>
          <div class="tile-card col4" style="top:0"><h3>Maintenance &amp; Service Plans</h3><p>Quarterly service options to keep your lighting system running smoothly, season after season.</p></div>
          <div class="tile-photo col4" style="top:33px;height:86px" role="img" aria-label="Lit house at dusk"></div>
        </div>
        <div class="cta-row"><p>Ready to see your home in a whole new light?</p><div class="btn btn-primary">Request a Custom Quote</div></div>
      </section>

      <section class="testimonials">
        <h2>What Our Clients Are Saying</h2>
        <article class="quote-card q1"><div class="stars">★★★★★</div><p>We were blown away by how our backyard transformed at night. Corwin Beacon delivered exactly what they promised — elegance and safety in one.</p><cite>Nora P., Homeowner</cite></article>
        <article class="quote-card q2"><div class="stars">★★★★★</div><p>Their team was so professional and easy to work with. The lighting made our entire property feel elevated.</p><cite>Gavin T., Real Estate Developer</cite></article>
        <article class="quote-card q3"><div class="stars">★★★★★</div><p>I loved that we could try a demo before committing. Derek and his team exceeded expectations!</p><cite>Elise W., Event Host</cite></article>
        <div class="dots"><i></i><i></i><i></i><i></i></div>
      </section>
    </div>
  </div>

</div>
</body>
</html>
```